Website design and coding for new consultancy company

I need to have a full website designed for a new consultancy business I'm trying to establish. It's called BrightPath consult. I need an English version to begin with, and then there should be a Danish version as well, but I'll translate that myself. Just be aware that I need two language versions. The consultancy field that I'm targeting is Leadership - and specialist development. I offer to facilitate corporate academies for global companies as well as specific workshops within leadership- or team development, strategy sessions, personal coaching and facilitation of D&I (Diversity and inclusion) workshops. BTW my logo is not in high resolution - I need that as well.

Target Market(s)

Larger companies that has a need for developing their inhouse leadership capabilities or that wants to develop their specialists to take on more responsibility.

Industry/Entity Type

Consultancy business

Coding

Coded - Design and coding required

Number of Pages Required

5+ page

Requirements
Must have
• Introduction site with a catch phrase. Book a meeting. Services that's beeing offered. Blog site with white papers etc. Language toggle (Danish/English). Cases/testimonials. About site. Contact site.

```html
<!DOCTYPE html>
<html lang="en">
<head>
<meta charset="utf-8">
<title>BrightPath consult – Improving Performance</title>
<link href="https://fonts.googleapis.com/css2?family=Poppins:ital,wght@0,400;0,500;0,600;0,700;0,800;1,400;1,600&display=swap" rel="stylesheet">
<style>
:root{
  --blue:#2a86cf;
  --blue-dark:#1f6fae;
  --orange:#f7941d;
  --ink:#141414;
  --dark:#1b1b1b;
  --text:#555;
  --grey-bg:#efefef;
  --card-border:#c9c9c9;
  --white:#fff;
}
*{box-sizing:border-box;margin:0;padding:0}
html,body{width:1200px;height:5080px;overflow:hidden;background:var(--white)}
body{font-family:"Poppins",sans-serif;color:var(--text);position:relative}
.abs{position:absolute}
a{text-decoration:none;color:inherit}
.btn{position:absolute;display:flex;align-items:center;justify-content:center;border-radius:30px;background:var(--orange);color:var(--white);font-weight:700;font-size:14px;letter-spacing:.3px}
.btn.dark{background:var(--ink)}
.photo{position:absolute}

/* header */
.brand{position:absolute;left:78px;top:22px;font-weight:800;font-size:40px;color:var(--ink);letter-spacing:-1px;line-height:1}
.call{position:absolute;left:786px;top:22px}
.call-icon{position:absolute;left:-3px;top:8px;width:38px;height:38px;border-radius:50%;background:var(--ink)}
.call small{position:absolute;left:48px;top:0;font-size:14px;font-weight:600;color:var(--ink);white-space:nowrap}
.call strong{position:absolute;left:48px;top:20px;font-size:24px;font-weight:700;color:var(--blue);white-space:nowrap}
.lang{position:absolute;left:1048px;top:30px;display:flex;align-items:center;gap:8px;font-size:14px;font-weight:600;color:var(--ink)}
.lang span.dot{width:36px;height:36px;border-radius:50%;background:var(--ink);display:block}

.nav{position:absolute;left:0;top:95px;width:1200px;height:57px;background:var(--blue)}
.nav ul{list-style:none;display:flex;position:absolute;left:75px;top:0;height:57px;align-items:center;gap:0}
.nav li{color:var(--white);font-size:15px;font-weight:600;margin-right:36px}
.nav li.active{color:var(--ink);border-bottom:2px solid var(--ink)}
.book{position:absolute;left:924px;top:95px;width:276px;height:57px;background:var(--orange);clip-path:polygon(0 0,100% 0,100% 100%,28px 100%);display:flex;align-items:center;justify-content:center;color:var(--white);font-weight:700;font-size:18px;gap:10px;padding-left:20px}

/* hero */
.hero{position:absolute;left:0;top:152px;width:1200px;height:680px;background:linear-gradient(100deg,#161410 0%,#3b3228 38%,#8a7a66 62%,#cfc8bb 85%,#e6e2d8 100%)}
.hero h1{position:absolute;left:72px;top:178px;font-size:66px;font-weight:700;color:var(--white);letter-spacing:1px}
.hero h2{position:absolute;left:74px;top:262px;font-size:33px;font-weight:700;color:var(--white);line-height:42px}
.hero .btn{left:75px;top:365px;width:256px;height:46px;font-size:15px}
.dots{position:absolute;left:72px;top:525px;display:flex;gap:10px}
.dots i{width:11px;height:11px;border-radius:50%;background:var(--white);display:block}
.dots i.on{background:var(--orange)}
.sheet{position:absolute;left:0;top:752px;width:1200px;height:4330px;background:var(--white);border-radius:110px 110px 0 0}

/* welcome */
.accent{position:absolute;background:var(--blue);border-radius:24px}
.welcome-photo{left:75px;top:821px;width:513px;height:403px;border-radius:24px;background:linear-gradient(135deg,#d9d6cf,#8e8a82 55%,#46505e)}
.welcome h3{position:absolute;left:616px;top:826px;font-size:46px;font-weight:400;color:var(--ink);line-height:52px}
.welcome h3 b{font-weight:800;display:block}
.welcome em{position:absolute;left:616px;top:936px;font-size:32px;font-weight:600;font-style:italic;color:var(--blue)}
.welcome p{position:absolute;left:616px;top:980px;width:512px;font-size:13.5px;line-height:24px}
.welcome .btn{left:616px;top:1172px;width:180px;height:50px}

/* services */
.services{position:absolute;left:0;top:1319px;width:1200px;height:616px;background:var(--blue);border-radius:90px}
.section-title{position:absolute;left:0;width:1200px;text-align:center;font-size:44px;color:var(--ink);font-weight:400}
.section-title b{font-weight:800}
.services .section-title{top:62px;color:var(--white)}
.svc{position:absolute;top:161px;width:329px;height:356px;background:var(--white);border-radius:14px;overflow:hidden;text-align:center}
.svc .photo{left:0;top:0;width:100%;height:175px}
.svc h4{position:absolute;top:203px;width:100%;font-size:19px;font-weight:600;color:var(--blue)}
.svc p{position:absolute;top:236px;left:30px;width:269px;font-size:12.5px;line-height:24px}
.svc-btn{top:492px;width:180px;height:46px}

/* why */
.why-sub{position:absolute;top:2070px;width:1200px;text-align:center;font-style:italic;font-size:18px;color:var(--ink);font-weight:500}
.why{position:absolute;top:2136px;width:242px;height:292px;border:1.5px solid var(--card-border);border-radius:12px;text-align:center}
.why.hl{background:linear-gradient(160deg,#14233a,#1f5f9a 60%,#2a86cf);border-color:transparent}
.why svg{position:absolute;left:71px;top:24px}
.why h4{position:absolute;top:150px;width:100%;font-size:17.5px;font-weight:600;color:var(--blue)}
.why p{position:absolute;top:180px;left:18px;width:206px;font-size:13px;line-height:24px}
.why.hl h4,.why.hl p{color:var(--white)}

/* about */
.about{position:absolute;left:0;top:2503px;width:1200px;height:432px;background:var(--dark);border-radius:90px}
.about h3{position:absolute;left:75px;top:66px;font-size:46px;font-weight:400;color:var(--white)}
.about h3 b{font-weight:800}
.about p{position:absolute;left:75px;top:134px;width:610px;font-size:13.5px;line-height:24px;color:var(--white)}
.about .btn{left:75px;top:304px;width:180px;height:48px}
.ring{position:absolute;left:752px;top:29px;width:376px;height:376px;border-radius:50%;border:2px solid var(--white)}
.portrait{position:absolute;left:776px;top:53px;width:328px;height:328px;border-radius:50%;background:linear-gradient(160deg,#e8e8e8,#cfcfcf 55%,#26374f)}

/* testimonials */
.tst{position:absolute;top:3095px;width:330px;height:271px;border:1.5px solid var(--card-border);border-radius:12px;text-align:center}
.tst.mid{background:#f2f2f2;border-color:transparent}
.avatar{position:absolute;left:121px;top:25px;width:88px;height:88px;border-radius:50%;background:var(--ink)}
.tst .q{position:absolute;left:0;top:100px;width:100%;font-size:60px;font-weight:800;color:var(--orange);line-height:1}
.tst p{position:absolute;left:22px;top:144px;width:286px;font-size:13px;line-height:24px;font-style:italic}
.tst h5{position:absolute;top:220px;width:100%;font-size:14px;font-weight:600;color:var(--blue)}
.tdots{position:absolute;left:572px;top:3418px;display:flex;gap:5px}
.tdots i{width:10px;height:10px;border-radius:50%;background:#8a8a8a;display:block}
.tdots i.on{background:var(--blue)}

/* articles */
.articles{position:absolute;left:0;top:3490px;width:1200px;height:616px;background:var(--grey-bg);border-radius:90px}
.art{position:absolute;top:152px;width:330px}
.art .photo{left:0;top:0;width:330px;height:213px;border-radius:12px}
.art h4{position:absolute;top:232px;width:330px;font-size:23px;font-weight:600;color:var(--blue);line-height:31px}
.art p{position:absolute;top:300px;width:330px;font-size:13px;line-height:23px}
.art a{position:absolute;top:378px;font-size:13px;font-weight:700;color:var(--orange)}

/* contact */
.cta h3{position:absolute;left:75px;top:4200px;font-size:44px;font-weight:400;color:var(--ink);line-height:48px}
.cta h3 b{font-weight:800}
.cta p{position:absolute;left:75px;top:4352px;width:470px;font-size:13.5px;line-height:24px}
.info{position:absolute;left:75px}
.info i{position:absolute;left:0;top:6px;width:40px;height:40px;border-radius:50%;background:var(--orange);display:flex;align-items:center;justify-content:center}
.info b{position:absolute;left:55px;top:0;font-size:18px;color:var(--blue);font-weight:600;white-space:nowrap}
.info span{position:absolute;left:55px;top:28px;font-size:14px;color:#333;white-space:nowrap}
.quick{position:absolute;left:616px;top:4193px;width:511px;height:426px;background:var(--blue);border-radius:6px}
.quick h3{position:absolute;left:24px;top:18px;font-size:46px;font-weight:700;color:var(--white)}
.field{position:absolute;background:var(--white);border-radius:22px;font-size:13.5px;color:#888;padding:14px 18px}
.quick .btn{left:22px;top:343px;width:180px;height:48px}

/* footer */
.footer{position:absolute;left:0;top:4684px;width:1200px;height:396px;background:var(--dark);border-radius:90px 90px 0 0;color:var(--white)}
.foot-brand{position:absolute;left:75px;top:133px;font-size:46px;font-weight:800;letter-spacing:-1px;line-height:1}
.foot-tag{position:absolute;left:78px;top:188px;font-size:12px;font-weight:600;letter-spacing:2px}
.fcol{position:absolute;top:80px}
.fcol h6{font-size:15px;font-weight:700;margin-bottom:12px}
.fcol li{list-style:none;font-size:13.5px;line-height:30.5px}
.social{display:flex;gap:16px;margin-top:4px}
.social i{width:20px;height:20px;border-radius:50%;background:var(--white);display:block}
.rule{position:absolute;left:0;top:324px;width:1200px;height:1px;background:#3a3a3a}
.copy{position:absolute;top:352px;width:1200px;text-align:center;font-size:12px}
</style>
</head>
<body>

<header>
  <div class="brand">BRIGHTPATH</div>
  <div class="call">
    <span class="call-icon"></span>
    <svg class="abs" style="left:8px;top:19px" width="16" height="16" viewBox="0 0 24 24"><path d="M6.6 10.8c1.4 2.8 3.8 5.1 6.6 6.6l2.2-2.2c.3-.3.7-.4 1-.2 1.1.4 2.3.6 3.6.6.6 0 1 .4 1 1V20c0 .6-.4 1-1 1C10.6 21 3 13.4 3 4c0-.6.4-1 1-1h3.5c.6 0 1 .4 1 1 0 1.3.2 2.5.6 3.6.1.3 0 .7-.2 1z" fill="#fff"/></svg>
    <small>Call Us Today:</small>
    <strong>+100-555-0142</strong>
  </div>
  <div class="lang"><span class="dot"></span>EN</div>
</header>

<nav class="nav">
  <ul>
    <li class="active">HOME</li><li>ABOUT</li><li>SERVICES</li><li>CASE STUDIES</li><li>BLOG</li><li>LATEST NEWS</li><li>CONTACT US</li>
  </ul>
</nav>
<a class="book"><svg width="18" height="18" viewBox="0 0 24 24"><rect x="2" y="2" width="20" height="20" rx="3" fill="#fff"/><path d="M7 12l3.5 3.5L17 9" stroke="#f7941d" stroke-width="2.6" fill="none"/></svg>BOOK A CALL</a>

<section class="hero" role="img" aria-label="Consultant presenting at a whiteboard covered with sticky notes">
  <h1>BRIGHTPATH</h1>
  <h2>Empowering Global Leaders<br>&amp; Teams to Thrive</h2>
  <a class="btn">BOOK A CONSULTATION</a>
  <div class="dots"><i></i><i class="on"></i><i></i><i></i></div>
</section>

<div class="sheet"></div>

<section class="welcome">
  <div class="accent" style="left:60px;top:808px;width:232px;height:200px"></div>
  <div class="accent" style="left:328px;top:1040px;width:230px;height:196px"></div>
  <div class="photo welcome-photo" role="img" aria-label="Team meeting around a table with laptops"></div>
  <h3>WELCOME TO<b>BRIGHTPATH</b></h3>
  <em>Improving Performance</em>
  <p>Nemo enim ipsam voluptatem quia voluptas sit aspernatur aut odit aut fugit, sed quia consequuntur magni dolores eos qui ratione voluptatem sequi nesciunt. Neque porro quisquam est, qui dolorem ipsum quia dolor sit amet, consectetur, adipisci velit, sed quia non numquam eius modi tempora incidunt ut labore et dolore magnam aliquam quaerat voluptatem aute irure dolor in reprehenderit in voluptate velit esse cillum dolore eu fugiat nulla pariatur.</p>
  <a class="btn">READ MORE</a>
</section>

<section class="services">
  <h3 class="section-title"><b>OUR SERVICES</b> OFFER</h3>
  <article class="svc" style="left:75px">
    <div class="photo" role="img" aria-label="Trainer presenting to a corporate group" style="background:linear-gradient(135deg,#e4e4e2,#a9adb0 60%,#3d4a5c)"></div>
    <h4>CORPORATE ACADEMIES</h4>
    <p>Keep your trees healthy, your garden beautiful and your property safe with professional tree pruning.</p>
  </article>
  <article class="svc" style="left:436px">
    <div class="photo" role="img" aria-label="Workshop leader at a flip chart with participants" style="background:linear-gradient(135deg,#ecebe7,#b7b4ad 60%,#4a4a4c)"></div>
    <h4>WORKSHOPS &amp; PROGRAMS</h4>
    <p>Whether it's been damaged by a storm or simply no longer desired on your property, trust Home GROVE.</p>
  </article>
  <article class="svc" style="left:797px">
    <div class="photo" role="img" aria-label="One-to-one coaching session in an office" style="background:linear-gradient(135deg,#cfd6dc,#8a97a3 55%,#2d3a4c)"></div>
    <h4>PERSONAL COACHING</h4>
    <p>Removing unsightly stumps will improve your garden's appearance. Home GROVE has the equipment to remove.</p>
  </article>
  <a class="btn svc-btn" style="left:149px">READ MORE</a>
  <a class="btn dark svc-btn" style="left:510px">READ MORE</a>
  <a class="btn svc-btn" style="left:872px">READ MORE</a>
</section>

<section>
  <h3 class="section-title" style="top:1996px"><b>WHY CHOOSE</b> US</h3>
  <p class="why-sub">Excepteur sint occaecat cupidatat non proidentsunt in culpa qui officia.</p>

  <div class="why" style="left:75px">
    <svg width="100" height="100" viewBox="0 0 100 100"><circle cx="50" cy="50" r="46" fill="none" stroke="#2a86cf" stroke-width="5"/><circle cx="50" cy="42" r="8" fill="#141414"/><circle cx="32" cy="48" r="6" fill="#141414"/><circle cx="68" cy="48" r="6" fill="#141414"/><path d="M36 68a14 12 0 0 1 28 0z M20 68a12 10 0 0 1 20-4v4z M60 64a12 10 0 0 1 20 4z" fill="#141414"/></svg>
    <h4>STRONGER LEADERS</h4>
    <p>Nemo enim ipsam voluptatem quia voluptas sit aspernatur aut odit aut fugit, sed quia consequuntur.</p>
  </div>
  <div class="why hl" style="left:345px">
    <svg width="100" height="100" viewBox="0 0 100 100"><circle cx="50" cy="50" r="46" fill="none" stroke="#2a86cf" stroke-width="5"/><path d="M33 52l11 11 23-25" stroke="#fff" stroke-width="7" fill="none" stroke-linecap="round" stroke-linejoin="round"/></svg>
    <h4>COHESIVE TEAMS</h4>
    <p>Nemo enim ipsam voluptatem quia voluptas sit aspernatur aut odit aut fugit, sed quia consequuntur.</p>
  </div>
  <div class="why" style="left:614px">
    <svg width="100" height="100" viewBox="0 0 100 100"><circle cx="50" cy="50" r="46" fill="none" stroke="#2a86cf" stroke-width="5"/><circle cx="50" cy="44" r="14" fill="#141414"/><rect x="43" y="58" width="14" height="10" rx="2" fill="#141414"/></svg>
    <h4>DIVERSITY IMPACT</h4>
    <p>Nemo enim ipsam voluptatem quia voluptas sit aspernatur aut odit aut fugit, sed quia consequuntur.</p>
  </div>
  <div class="why" style="left:884px">
    <svg width="100" height="100" viewBox="0 0 100 100"><circle cx="50" cy="50" r="46" fill="none" stroke="#2a86cf" stroke-width="5"/><rect x="37" y="28" width="26" height="44" fill="#141414"/><g fill="#fff"><rect x="42" y="33" width="5" height="5"/><rect x="53" y="33" width="5" height="5"/><rect x="42" y="43" width="5" height="5"/><rect x="53" y="43" width="5" height="5"/><rect x="42" y="53" width="5" height="5"/><rect x="53" y="53" width="5" height="5"/><rect x="47" y="63" width="6" height="9"/></g></svg>
    <h4>COMPANY CULTURE</h4>
    <p>Nemo enim ipsam voluptatem quia voluptas sit aspernatur aut odit aut fugit, sed quia consequuntur.</p>
  </div>
</section>

<section class="about">
  <h3>ABOUT <b>ME</b></h3>
  <p>Nemo enim ipsam voluptatem quia voluptas sit aspernatur aut odit aut fugit, sed quia consequuntur magni dolores eos qui ratione voluptatem sequi nesciunt. Neque porro quisquam est, qui dolorem ipsum quia dolor sit amet, consectetur, adipisci velit, sed quia non numquam eius modi tempora incidunt ut labore et dolore magnam aliquam quaerat voluptatem aute irure dolor in reprehenderit in voluptate velit esse cillum dolore eu fugiat nulla pariatur.</p>
  <a class="btn">READ MORE</a>
  <div class="ring"></div>
  <div class="portrait" role="img" aria-label="Portrait of the founder in a suit"></div>
</section>

<section>
  <h3 class="section-title" style="top:2994px"><b>CUSTOMER</b> TESTIMONIALS</h3>
  <div class="tst" style="left:75px"><span class="avatar"></span><span class="q">”</span><p>" Duis aute irure dolor in reprehenderit in voluptate velit esse cillum dolore eu fugiat nulla pariatur."</p><h5>Marianne</h5></div>
  <div class="tst mid" style="left:436px"><span class="avatar"></span><span class="q">”</span><p>" Duis aute irure dolor in reprehenderit in voluptate velit esse cillum dolore eu fugiat nulla pariatur."</p><h5>Marianne</h5></div>
  <div class="tst" style="left:797px"><span class="avatar"></span><span class="q">”</span><p>" Duis aute irure dolor in reprehenderit in voluptate velit esse cillum dolore eu fugiat nulla pariatur."</p><h5>Marianne</h5></div>
  <div class="tdots"><i class="on"></i><i></i><i></i><i></i></div>
</section>

<section class="articles">
  <h3 class="section-title" style="top:62px">LATEST <b>ARTICLES</b></h3>
  <article class="art" style="left:75px">
    <div class="photo" role="img" aria-label="Business consultant at a desk with documents" style="background:linear-gradient(135deg,#d8d6d0,#8d8b86 55%,#34404f)"></div>
    <h4>Excepteur sint occaecat cupidatat</h4>
    <p>Duis aute irure dolor in reprehenderit in voluptate velit esse cillum dolore eu fugiat nulla pariatur</p>
    <a>READ MORE</a>
  </article>
  <article class="art" style="left:436px">
    <div class="photo" role="img" aria-label="Two colleagues reviewing a tablet in a dark office" style="background:linear-gradient(135deg,#2a2d33,#4a5260 55%,#1a1c20)"></div>
    <h4>Excepteur sint occaecat cupidatat</h4>
    <p>Duis aute irure dolor in reprehenderit in voluptate velit esse cillum dolore eu fugiat nulla pariatur</p>
    <a>READ MORE</a>
  </article>
  <article class="art" style="left:797px">
    <div class="photo" role="img" aria-label="Diverse team discussing around a tablet" style="background:linear-gradient(135deg,#e2e2de,#a4a8ac 55%,#3a4656)"></div>
    <h4>Excepteur sint occaecat cupidatat</h4>
    <p>Duis aute irure dolor in reprehenderit in voluptate velit esse cillum dolore eu fugiat nulla pariatur</p>
    <a>READ MORE</a>
  </article>
</section>

<section class="cta">
  <h3><b>CALL US TODAY,</b><br>GET A FREE<br>CONSULTANT</h3>
  <p>Duis aute irure dolor in reprehenderit in voluptate velit esse cillum dolore eu fugiat nulla pariatur.</p>
  <div class="info" style="top:4430px"><i><svg width="18" height="18" viewBox="0 0 24 24"><path d="M12 2a7 7 0 0 0-7 7c0 5 7 13 7 13s7-8 7-13a7 7 0 0 0-7-7zm0 9.5A2.5 2.5 0 1 1 12 6.5a2.5 2.5 0 0 1 0 5z" fill="#fff"/></svg></i><b>Address</b><span>48 Harbour Lane, Suite 210, Aarhus 8000, Denmark</span></div>
  <div class="info" style="top:4492px"><i><svg width="18" height="18" viewBox="0 0 24 24"><path d="M6.6 10.8c1.4 2.8 3.8 5.1 6.6 6.6l2.2-2.2c.3-.3.7-.4 1-.2 1.1.4 2.3.6 3.6.6.6 0 1 .4 1 1V20c0 .6-.4 1-1 1C10.6 21 3 13.4 3 4c0-.6.4-1 1-1h3.5c.6 0 1 .4 1 1 0 1.3.2 2.5.6 3.6.1.3 0 .7-.2 1z" fill="#fff"/></svg></i><b>Phone No</b><span>+100-555-0142</span></div>
  <div class="info" style="top:4554px"><i><svg width="18" height="18" viewBox="0 0 24 24"><rect x="3" y="5" width="18" height="14" rx="2" fill="#fff"/><path d="M3 7l9 6 9-6" stroke="#f7941d" stroke-width="2" fill="none"/></svg></i><b>Email</b><span>hello@brightpathmail.com</span></div>

  <form class="quick">
    <h3>QUICK CONTACT</h3>
    <div class="field" style="left:22px;top:97px;width:228px;height:49px">Name</div>
    <div class="field" style="left:261px;top:97px;width:228px;height:49px">Email Address</div>
    <div class="field" style="left:22px;top:158px;width:228px;height:51px">Phone No</div>
    <div class="field" style="left:261px;top:158px;width:228px;height:51px">Services<span style="position:absolute;right:18px;top:13px;color:#555">⇕</span></div>
    <div class="field" style="left:22px;top:221px;width:467px;height:110px">Message</div>
    <a class="btn">SUBMIT</a>
  </form>
</section>

<footer class="footer">
  <div class="foot-brand">BRIGHTPATH</div>
  <div class="foot-tag">WWW.BRIGHTPATHCONSULT.DK</div>
  <div class="fcol" style="left:424px"><h6>SITE MAP</h6><ul><li>Home</li><li>About</li><li>Services</li><li>Case Studies</li><li>Latest News</li><li>Contact Us</li></ul></div>
  <div class="fcol" style="left:665px"><h6>RESOURCES</h6><ul><li>Duis aute irure</li><li>Dolor in reprehenderit</li><li>Voluptate velit</li><li>Esse cillum</li><li>Dolore eu fugiat</li><li>Nulla pariatur</li></ul></div>
  <div class="fcol" style="left:920px"><h6>FOLLOW US</h6><div class="social"><i></i><i></i><i></i><i></i><i></i></div></div>
  <div class="rule"></div>
  <p class="copy">© Copyright 2025 Company Name All Rights Reserved.</p>
</footer>

</body>
</html>
```